Business Card Design (NEW FILES)

ATTENTION: New vector files are available. Please update your design to reflect/use the new (better resolution) logo images.

Seeking a unique and professional business card design for a commercial drone photography/videography business. The layout should feature
the logo (attached) and include the following information:
Owen Tarrick
614-502-7738
www.skylarkreelworks.example
NRD Certified Remote Pilot

Owen Tarrick

```html
<!DOCTYPE html>
<html lang="en">
<head>
<meta charset="utf-8">
<title>Skylark Reelworks – Business Card</title>
<link rel="stylesheet" href="https://fonts.googleapis.com/css2?family=Open+Sans:wght@400;600;700&display=swap">
<style>
  :root {
    --bg: #e9e9ec;
    --orange: #ec8b55;
    --orange-deep: #d9763f;
    --navy: #141a4a;
    --white: #ffffff;
    --card-w: 540px;
    --card-h: 309px;
  }
  * { box-sizing: border-box; margin: 0; padding: 0; }
  html, body {
    width: 1200px; height: 780px; overflow: hidden;
    background: var(--bg);
    font-family: "Open Sans", Arial, sans-serif;
  }
  .canvas {
    position: relative; width: 1200px; height: 780px;
    display: flex; align-items: center; justify-content: center; gap: 40px;
  }
  .card {
    position: relative; width: var(--card-w); height: var(--card-h);
    border-radius: 22px; overflow: hidden;
  }

  /* Front */
  .card-front { background: var(--orange); display: flex; align-items: center; justify-content: center; gap: 14px; }
  .front-mark { width: 30px; height: 30px; border-radius: 50%; background: var(--orange-deep); }
  .front-name { font-size: 38px; font-weight: 600; color: var(--orange-deep); letter-spacing: 1px; text-transform: uppercase; }

  /* Back */
  .card-back { background: var(--navy); border-bottom: 6px solid var(--orange); border-left: 4px solid var(--orange); }
  .brand { position: absolute; left: 34px; top: 70px; display: flex; align-items: center; gap: 10px; }
  .brand-mark { width: 16px; height: 16px; border-radius: 50%; background: var(--orange); }
  .brand-name { font-size: 26px; font-weight: 600; color: var(--white); letter-spacing: 1px; text-transform: uppercase; line-height: 1; }

  .person { position: absolute; right: 46px; top: 34px; text-align: right; }
  .person-name { font-size: 26px; font-weight: 700; line-height: 1.1; }
  .person-name .first { color: var(--orange); }
  .person-name .last { color: var(--white); }
  .person-role { font-size: 13px; color: var(--white); margin-top: 2px; }
  .accent-bar { position: absolute; right: 0; top: 34px; width: 26px; height: 44px; background: var(--orange); }

  .credentials { position: absolute; left: 34px; top: 160px; color: var(--white); font-size: 14px; line-height: 1.4; }
  .contact { position: absolute; left: 34px; top: 208px; list-style: none; color: var(--white); font-size: 13.5px; }
  .contact li { display: flex; align-items: center; gap: 10px; line-height: 24px; }
  .contact svg { width: 14px; height: 14px; flex: none; }
</style>
</head>
<body>
<main class="canvas">
  <section class="card card-front" aria-label="Card front">
    <span class="front-mark"></span>
    <span class="front-name">Skylark Reelworks</span>
  </section>

  <section class="card card-back" aria-label="Card back">
    <div class="brand">
      <span class="brand-mark"></span>
      <span class="brand-name">Skylark Reelworks</span>
    </div>

    <div class="accent-bar"></div>
    <div class="person">
      <p class="person-name"><span class="first">Owen</span> <span class="last">Tarrick</span></p>
      <p class="person-role">Owner</p>
    </div>

    <div class="credentials">
      <p>NRD Certified Remote Pilot</p>
      <p>Fully Insured</p>
    </div>

    <ul class="contact">
      <li>
        <svg viewBox="0 0 24 24" fill="#ec8b55" aria-hidden="true"><path d="M6.6 10.8a15 15 0 0 0 6.6 6.6l2.2-2.2a1 1 0 0 1 1-.25 11.4 11.4 0 0 0 3.6.57 1 1 0 0 1 1 1V20a1 1 0 0 1-1 1A17 17 0 0 1 3 4a1 1 0 0 1 1-1h3.5a1 1 0 0 1 1 1c0 1.25.2 2.45.57 3.57a1 1 0 0 1-.25 1z"/></svg>
        614-502-7738
      </li>
      <li>
        <svg viewBox="0 0 24 24" fill="none" stroke="#ec8b55" stroke-width="2" aria-hidden="true"><circle cx="12" cy="12" r="9"/><path d="M3 12h18M12 3a14 14 0 0 1 0 18M12 3a14 14 0 0 0 0 18"/></svg>
        www.skylarkreelworks.example
      </li>
      <li>
        <svg viewBox="0 0 24 24" fill="none" stroke="#ec8b55" stroke-width="2" aria-hidden="true"><rect x="3" y="5" width="18" height="14" rx="1"/><path d="M3 6l9 7 9-7"/></svg>
        info@skylarkreelworks.example
      </li>
    </ul>
  </section>
</main>
</body>
</html>
```